BOLD & MINIMALIST DESIGN NEEDED

We want a very bold but minimalistic business card design that is impactful and utilizes both sides of the business card. Our current logo is included for your use.

We want bold fonts and good use of negative space. We don't want the logo to overpower the design.

Target Market(s)

Professionals who are building new commercial buildings.

Industry/Entity Type

Construction

Contact Information for Business Card

Name, Title, email, office phone, cell phone, website

Font styles to use
Serif
Sans Serif

Requirements
Must have
• Bold design!

```html
<!DOCTYPE html>
<html lang="en">
<head>
<meta charset="utf-8">
<title>Ridgeline Design + Build — Business Card</title>
<link rel="stylesheet" href="https://fonts.googleapis.com/css2?family=Source+Sans+3:wght@300;400;700;800&display=swap">
<style>
  :root {
    --lime: #adf326;
    --ink: #0a0c0b;
    --paper: #cccccc;
    --white: #ffffff;
    --font: "Source Sans 3", "Source Sans Pro", Arial, sans-serif;
  }
  * { margin: 0; padding: 0; box-sizing: border-box; }
  html, body {
    width: 1200px; height: 1198px; overflow: hidden;
    background: var(--paper);
    font-family: var(--font);
  }
  .canvas { position: relative; width: 1200px; height: 1198px; }

  .card {
    position: absolute;
    width: 638px; height: 354px;
    background: var(--lime);
    overflow: hidden;
  }
  .card--front { left: 271px; top: 210px; }
  .card--back  { left: 273px; top: 651px; }

  .card__art { position: absolute; inset: 0; width: 100%; height: 100%; }

  .brand {
    position: absolute;
    display: flex; align-items: center; gap: 10px;
    font-family: var(--font);
    font-weight: 800;
    color: var(--white);
    letter-spacing: 0.02em;
    white-space: nowrap;
    transform: translate(-50%, -50%);
  }
  .brand__mark { background: var(--white); flex: none; }
  .card--front .brand { left: 182px; top: 182px; font-size: 31px; }
  .card--front .brand__mark { width: 22px; height: 22px; }
  .card--front .brand__sub { font-size: 31px; }

  .card--back .brand { left: 88px; top: 290px; font-size: 16px; gap: 6px; }
  .card--back .brand__mark { width: 12px; height: 12px; }

  .back__panel {
    position: absolute; left: 0; top: 0;
    width: 181px; height: 100%;
    background: var(--ink);
  }

  .contact { position: absolute; left: 212px; top: 0; color: var(--ink); }
  .contact__name {
    position: absolute; top: 42px; white-space: nowrap;
    font-size: 27px; font-weight: 700; letter-spacing: 0.005em;
  }
  .contact__title {
    position: absolute; top: 76px; white-space: nowrap;
    font-size: 22px; font-weight: 300;
  }
  .contact__rule {
    position: absolute; top: 115px; left: 0;
    width: 266px; height: 3px; background: var(--white);
  }
  .contact__email {
    position: absolute; top: 208px; white-space: nowrap;
    font-size: 22px; font-weight: 400;
  }
  .contact__phone {
    position: absolute; white-space: nowrap;
    font-size: 19px; font-weight: 700;
  }
  .contact__phone--office { top: 240px; }
  .contact__phone--cell { top: 267px; }
  .contact__web {
    position: absolute; top: 294px; white-space: nowrap;
    font-size: 14px; font-weight: 700;
  }
</style>
</head>
<body>
<main class="canvas">

  <section class="card card--front" aria-label="Card front">
    <svg class="card__art" viewBox="0 0 638 354" preserveAspectRatio="none">
      <polygon points="474,0 638,0 638,354 393,354" fill="var(--ink)"
               role="img" aria-label="Line illustration of a commercial building in white and lime"/>
    </svg>
    <div class="brand">
      <span class="brand__mark"></span>
      <span>RIDGELINE</span>
    </div>
  </section>

  <section class="card card--back" aria-label="Card back">
    <div class="back__panel"></div>
    <div class="brand">
      <span class="brand__mark"></span>
      <span>RIDGELINE</span>
    </div>
    <div class="contact">
      <p class="contact__name">NAME LASTNAME</p>
      <p class="contact__title">YOUR TITTLE</p>
      <span class="contact__rule"></span>
      <p class="contact__email">YOUREMAILEXAMPLE@EMAIL.COM</p>
      <p class="contact__phone contact__phone--office">123 - 456 - 7890</p>
      <p class="contact__phone contact__phone--cell">123 - 456 - 7890</p>
      <p class="contact__web">YOURWEBSITEEXAMPLE.COM</p>
    </div>
  </section>

</main>
</body>
</html>
```